Flyer-Design für Hundephysiopraxis
Zielgruppe
Ich bin selbstständige Hundephysiotherapeutin / Hundeosteopathin /Hundefitnesstrainerin. Meine Zielgruppe sind Hundehalter bzw. allgemein Tierhalter (biete noch weitere Dinge für Hunde/Tiere an) aber auch Tierärzte.
Aufgabenstellung
Es wäre schön, wenn Sie die Texte ähnlich wie auf meiner Homepage gestalten (z.B. Infos aus der Startseite oder Therapieformen).
Prinzipiell sollte es eher natürlich, freundlich und nett gestaltet sein. Schlichtere Farben passend zum Logo.
Homepage: www.pfotenruhe-mitte.de
Bei den Maßen bin ich offen, hatte aber eher an diesen 'typischen Flyer' gedacht (3 seitiger Flyer mit Vorder und Rückseite) bin aber prinzipiell offen :)
Einen Beispiel Flyer habe ich drangehängt sowie z.B. schon ein paar Fotos die man ggf nutzen kann. Weitere Behandlunsfotos kann ich gerne nachreichen.
Die Flyer sollen hauptsächlich bei z.B. Tierärzten / Tierklinik / Tiernahrungsmärkte wie Kornbeutel ausgelegt werden damit Menschen die mich noch nicht kennen auf meine Arbeit aufmerksam werden.

```html
<!DOCTYPE html>
<html lang="de">
<head>
<meta charset="utf-8">
<title>Pfotenruhe Mitte – Flyer</title>
<link href="https://fonts.googleapis.com/css2?family=Kaushan+Script&family=Crimson+Text:wght@400;600;700&display=swap" rel="stylesheet">
<style>
:root{
  --orange:#e6950f;
  --orange-deep:#ec8a00;
  --yellow:#fbbf00;
  --rust:#c4541a;
  --blue:#3d7bc4;
  --purple:#5b2d8e;
  --teal:#00a6bd;
  --violet:#7b3b96;
  --ink:#1b1b1b;
  --sun:#fdf1df;
  --paper:#ffffff;
}
*{margin:0;padding:0;box-sizing:border-box}
html,body{width:1200px;height:1200px;overflow:hidden;background:#fff}
body{position:relative;font-family:"Crimson Text",Georgia,serif;color:var(--ink)}
.sheet{position:absolute;width:631px;height:447px;background:var(--paper);overflow:hidden;box-shadow:4px 6px 10px rgba(0,0,0,.18)}
.sheet--outer{left:284px;top:80px}
.sheet--inner{left:298px;top:628px}
.abs{position:absolute}
.script{font-family:"Kaushan Script",cursive}
.body-text{font-size:8.2px;line-height:10.8px;text-align:justify;hyphens:auto}
.body-text p+p{margin-top:10.8px}
.sun-glow{position:absolute;border-radius:50%;background:radial-gradient(circle,var(--sun) 0%,var(--sun) 55%,rgba(253,241,223,0) 72%)}
.placeholder{position:absolute}

/* outer sheet */
.contact-panel{left:0;top:0;width:206px;height:287px;background:var(--yellow)}
.contact-panel__top{position:absolute;left:0;top:0;width:206px;height:150px}
.contact-title{left:9px;top:154px;font-size:15px;color:#fff}
.contact-text{left:9px;top:174px;width:190px;font-size:8px;line-height:10.8px;font-weight:600}
.contact-text p+p{margin-top:10.8px}
.map{left:0;top:287px;width:206px;height:133px;background:linear-gradient(135deg,#eef0f3,#dfe3e8)}
.panel-rule{left:206px;top:0;width:1px;height:420px;background:var(--orange)}
.col-title{font-size:17px;color:var(--ink)}
.bach-title{left:226px;top:12px}
.bach-text{left:226px;top:48px;width:175px}
.bach-photo{left:226px;top:287px;width:175px;height:137px;background:linear-gradient(160deg,#6b4a35,#d9d2c8 55%,#f3f0ea)}
.brand{left:440px;top:75px;width:160px;text-align:center}
.brand__ring{width:86px;height:86px;border:4px solid var(--orange-deep);border-radius:50%;margin:0 auto 6px}
.brand__name{font-family:"Crimson Text",Georgia,serif;font-weight:700;font-size:20px;color:var(--rust);line-height:22px}
.brand__sub{font-size:7.5px;letter-spacing:2px;color:var(--rust);line-height:10px;margin-top:2px}
.cover-title{left:440px;top:212px;width:162px;text-align:center;font-size:15.5px;line-height:18px;color:var(--blue)}
.dog-figure{border-radius:45% 55% 40% 50%;background:var(--teal)}
.runner-figure{border-radius:40% 40% 30% 30%;background:var(--violet)}

/* inner sheet */
.heading-blue{font-size:13.5px;line-height:17px;color:var(--blue);text-align:center}
.motto{left:6px;top:40px;width:200px}
.motto-text{left:18px;top:79px;width:177px}
.signature{left:18px;top:308px;font-size:8px;color:var(--blue)}
.care{left:225px;top:40px;width:200px}
.services{left:226px;top:76px;width:200px;font-size:8.2px;line-height:10.8px}
.services__label{font-weight:700;font-size:9px;margin-bottom:10px}
.services ul{list-style:none;color:var(--purple)}
.leech{left:430px;top:40px;width:190px}
.leech-text{left:432px;top:77px;width:187px;text-align:left}
.inner-photo{left:216px;top:253px;width:141px;height:147px;background:linear-gradient(180deg,#5c6a52,#9aa39a 45%,#e9ebe8 85%,#fff)}
</style>
</head>
<body>

<!-- Outer side -->
<section class="sheet sheet--outer">
  <div class="sun-glow" style="left:190px;top:40px;width:260px;height:260px"></div>

  <div class="abs contact-panel">
    <svg class="contact-panel__top" viewBox="0 0 206 150" aria-hidden="true">
      <path d="M0 0H206V150C170 136 120 140 80 146C45 150 20 146 0 140Z" fill="var(--orange)"/>
    </svg>
    <div class="placeholder" role="img" aria-label="Foto: Therapeutin sitzt mit zwei Hunden auf einer Wiese"
         style="left:31px;top:11px;width:132px;height:132px;border-radius:50%;background:linear-gradient(160deg,#8fae6a,#5b7a3c 60%,#3a2d22)"></div>
  </div>
  <div class="abs script contact-title">Kontakt</div>
  <div class="abs contact-text">
    <p>E-mail: info@pfotenruhe-mitte.de</p>
    <p>Handy: 0176 55501234<br>gerne auch eine Nachricht per Messenger oder SMS</p>
    <p>Anschrift:<br>Marlene Hoff,<br>Talstr. 9,<br>35400 Musterau</p>
  </div>
  <div class="abs map placeholder" role="img" aria-label="Stadtplanausschnitt mit Standort der Praxis"></div>
  <div class="abs panel-rule"></div>

  <h2 class="abs script col-title bach-title">Bachblütenberatung</h2>
  <div class="abs body-text bach-text">
    <p>Bachblüten sind Extrakte aus Blüten, die auf störende Emotionen und Gefühle wie z.B. (Trennungs-)Angst, Unsicherheit, Aggression, Stress usw. positiv einwirken. Sie können bei Silvester, einer langen Autoreise, Umzug oder dem Tierarztbesuch unterstützen.</p>
    <p>Der Name stammt von Dr. Edwin Barlow (1886-1936), der diese Heilweise am Anfang des vorigen Jahrhunderts entdeckt hat. Seit mehr als 70 Jahren gelten Bachblüten als geeignetes Mittel bei emotionalen Problemen aller Art.</p>
    <p>Unter den über 30 Bachblüten teste ich aus, welche Blüte oder Blüten Deinen Hund optimal unterstützen.</p>
    <p>Speziell bei Tierschutzhunden konnte ich einige positive Entwicklungen dank der Bachblüten feststellen.</p>
  </div>
  <div class="abs placeholder bach-photo" role="img" aria-label="Foto: braun-weißer Spaniel"></div>

  <div class="abs brand">
    <div class="brand__ring"></div>
    <div class="brand__name">Pfotenruhe Mitte</div>
    <div class="brand__sub">Hundephysiotherapie<br>Marlene Hoff</div>
  </div>
  <h1 class="abs script cover-title">Hundephysiotherapie<br>&amp;<br>Hundeosteopathie (i.A.)</h1>

  <svg class="abs" style="left:0;top:380px" width="631" height="67" viewBox="0 0 631 67" aria-hidden="true">
    <path d="M0 40C120 28 260 30 400 40C500 47 570 42 631 30V67H0Z" fill="var(--orange-deep)"/>
    <path d="M0 44C120 33 260 35 400 45C500 52 570 47 631 35V67H0Z" fill="var(--yellow)"/>
  </svg>
  <div class="placeholder dog-figure" role="img" aria-label="Silhouette eines springenden Hundes" style="left:431px;top:383px;width:62px;height:50px"></div>
  <div class="placeholder runner-figure" role="img" aria-label="Silhouette einer laufenden Frau" style="left:558px;top:330px;width:62px;height:102px"></div>
</section>

<!-- Inner side -->
<section class="sheet sheet--inner">
  <div class="sun-glow" style="left:380px;top:-20px;width:290px;height:290px"></div>

  <h2 class="abs script heading-blue motto">Leben ist Bewegung und Bewegung ist Lebensqualität!</h2>
  <div class="abs body-text motto-text">
    <p>Rennen, laufen, springen, toben und spielen zeigt die Lebensfreude unserer Hunde! Wer keine Schmerzen hat, kann sich frei bewegen und hat Spaß dabei. Wenn unsere Hunde jedoch erkranken oder alt werden, dann benötigen sie unsere Unterstützung.</p>
    <p>Nach einem Unfall, bei Schmerzen oder Beschwerden im Rücken und in den Gelenken, nach Operationen oder bei Lahmheiten können Physiotherapie sowie Osteopathie helfen. Es lindert die Schmerzen, lockert verspannte Muskulatur, verbessert die Beweglichkeit oder stellt diese wieder her. Weiterhin baut Physiotherapie Muskulatur auf, fördert die Genesung und hilft im Alter fit zu bleiben.</p>
    <p>Ich helfe Deinem Hund gerne dabei, die Gesundheit und damit die Lebensqualität und Lebensfreude zurück zu erhalten.</p>
  </div>
  <div class="abs script signature">– Marlene Hoff</div>

  <h2 class="abs script heading-blue care">Für mich steht Dein Hund an erster Stelle. Therapie mit Herz.</h2>
  <div class="abs services">
    <div class="services__label">Leistung:</div>
    <ul>
      <li>Hundephysiotherapie</li>
      <li>Hundeosteopathie (i.A.)</li>
      <li>Breuß-Massage</li>
      <li>Dorn-Therapie</li>
      <li>Hundefitnesstrainer (i.A.)</li>
      <li>Blutegeltherapie</li>
      <li>Bachblütenberatung (siehe Rückseite)</li>
      <li>Tierkommunikation</li>
      <li>Edelsteintherapie</li>
      <li>Mykotherapie</li>
    </ul>
  </div>
  <div class="abs placeholder inner-photo" role="img" aria-label="Foto: schwarz-weißer Spaniel im Garten"></div>

  <h2 class="abs script heading-blue leech">Blutegeltherapie</h2>
  <div class="abs body-text leech-text">
    <p>Blutegel gehören zu der Unterklasse der Egel (Hirudinea) und werden in der Medizin schon lange zur Behandlung verschiedener Krankheiten eingesetzt.</p>
    <p>Sie haben einen Saugnapf, mit dem sie sich an die zu behandelnden Stellen festsetzen und Blut saugen. Das Speichel-Sekret des Blutegels, welches beim Beissen in die Wunde des Tieres gelangt, wirkt entzündungs- und gerinnungshemmend, schmerzlindernd und regt den Lymphfluss an.</p>
  </div>

  <svg class="abs" style="left:0;top:360px" width="631" height="87" viewBox="0 0 631 87" aria-hidden="true">
    <path d="M0 22C100 8 180 6 260 12C360 20 420 45 500 47C560 48 600 40 631 30V87H0Z" fill="var(--orange-deep)"/>
    <path d="M0 30C100 16 180 14 260 22C360 32 420 57 500 57C560 57 600 48 631 40V87H0Z" fill="var(--yellow)"/>
  </svg>
  <div class="placeholder dog-figure" role="img" aria-label="Silhouette eines rennenden Hundes" style="left:66px;top:340px;width:124px;height:96px"></div>
  <div class="placeholder runner-figure" role="img" aria-label="Silhouette einer laufenden Frau" style="left:497px;top:251px;width:116px;height:186px"></div>
</section>

</body>
</html>
```